Belmont Ridge Business Card Design Project

We have recently rebranded and would like to design new business cards that incorporate the corporate logo - double sided cards with corporate logo on one side and contact details on the other

Target Market(s)

Sophisticated and high net worth investors and finance industry professionals

Industry/Entity Type

Funds Management

Contact Information for Business Card

The card should prominently feature the company name and logo. Other details will be standard contact details for each staff member - name, address, phone, email, website

Colors
0054AA
0677BA
7BADD7
CADEEF
E8F1F8

Requirements
Must have
• Double-sided design with one side prominently featuring the corporate logo and the other side with all standard contact details

```html
<!DOCTYPE html>
<html lang="en">
<head>
<meta charset="utf-8">
<title>Belmont Ridge – Business Card</title>
<link href="https://fonts.googleapis.com/css2?family=Open+Sans:wght@400;600;700&display=swap" rel="stylesheet">
<style>
  :root {
    --backdrop: #ababab;
    --brand-navy: #1f4573;
    --accent-blue: #6699cc;
    --ink: #111111;
    --body-grey: #555555;
    --paper: #ffffff;
  }
  * { margin: 0; padding: 0; box-sizing: border-box; }
  html, body {
    width: 1200px;
    height: 1000px;
    overflow: hidden;
    background: var(--backdrop);
    font-family: "Open Sans", Arial, sans-serif;
  }
  .card {
    position: absolute;
    top: 338px;
    width: 514px;
    height: 296px;
  }
  .card--front {
    left: 57px;
    background: var(--brand-navy);
  }
  .card--back {
    left: 614px;
    background: var(--paper);
  }
  .wordmark {
    position: absolute;
    left: 44px;
    top: 196px;
    display: flex;
    align-items: center;
    gap: 12px;
    color: var(--paper);
    font-weight: 600;
    font-size: 31px;
    letter-spacing: 0.5px;
    line-height: 1;
  }
  .wordmark__mark {
    width: 16px;
    height: 16px;
    background: var(--paper);
  }
  .contact {
    position: absolute;
    right: 43px;
    top: 52px;
    text-align: right;
    font-size: 14px;
    line-height: 16.5px;
    color: var(--body-grey);
  }
  .contact__name {
    color: var(--accent-blue);
    font-weight: 700;
    letter-spacing: 1.5px;
    text-transform: uppercase;
  }
  .contact__role {
    color: var(--ink);
    font-weight: 700;
    letter-spacing: 1.5px;
    text-transform: uppercase;
  }
  .contact__group { margin-top: 17px; }
  .contact__web {
    margin-top: 17px;
    color: var(--brand-navy);
    font-weight: 700;
  }
</style>
</head>
<body>
  <section class="card card--front" aria-label="Card front">
    <div class="wordmark">
      <span class="wordmark__mark" aria-hidden="true"></span>
      <span class="wordmark__name">Belmont Ridge</span>
    </div>
  </section>

  <section class="card card--back" aria-label="Card back">
    <div class="contact">
      <p class="contact__name">Daniel Hartley</p>
      <p class="contact__role">Portfolio Manager</p>
      <div class="contact__group">
        <p>+02 9460 3175</p>
        <p>invest@belmont-ridge.com</p>
      </div>
      <div class="contact__group">
        <p>Level 14 Kestrel House,</p>
        <p>41 Carrow Street,</p>
        <p>Sydney NSW 2000</p>
      </div>
      <p class="contact__web">www.belmont-ridge.com</p>
    </div>
  </section>
</body>
</html>
```